Flyer for an anniversary promotion

2nd year anniversary promotion flyer for Copperleaf Dental (logo attached)
Size A4
Promotion runs from Now until 31st Dec 2024
Leave room for actual promotional text which will be in multiple languages (~50 words)
Brand associations
Modern, classy, high quality service, customer care

NOTE - Company SELLS to dental clinics but Copperleaf is a dental products company, not dentists/dental clinics/etc.

Plumvistar wants this to be 300+ words

Target Market(s)

Dental clinics

Industry/Entity Type

Dental

Requirements
Should not have
• Don't use images of teeth

```html
<!DOCTYPE html>
<html lang="en">
<head>
<meta charset="utf-8">
<title>Copperleaf Dental – 2nd Anniversary Flyer</title>
<link href="https://fonts.googleapis.com/css2?family=Great+Vibes&family=PT+Sans:wght@400;700&family=Cinzel:wght@400;600&family=Noto+Serif+TC:wght@500&display=swap" rel="stylesheet">
<style>
  :root {
    --page-bg: #e9ebee;
    --navy: #2a3593;
    --cream: #f6f0c6;
    --sky-top: #f3f1e6;
    --sky-mid: #3f9fe0;
    --sky-low: #66bde9;
    --stripe-green: #2bb58a;
    --stripe-blue: #1a6fc0;
    --stripe-teal: #17b5c4;
    --band-blue: #1c7cc6;
    --ink-dark: #1d1d2b;
    --white: #ffffff;
    --frost: rgba(225, 243, 255, 0.55);
  }
  * { margin: 0; padding: 0; box-sizing: border-box; }
  html, body { width: 1200px; height: 856px; overflow: hidden; }
  body { background: var(--page-bg); position: relative; font-family: "PT Sans", sans-serif; }

  .flyer {
    position: absolute; left: 311px; top: 20px;
    width: 577px; height: 816px;
    background: var(--white);
    overflow: hidden;
    box-shadow: 0 4px 18px rgba(0,0,0,0.18);
  }
  .stripe { position: absolute; left: 0; width: 100%; height: 9px; display: flex; }
  .stripe span { height: 100%; }
  .stripe span:nth-child(1) { width: 33%; background: var(--stripe-green); }
  .stripe span:nth-child(2) { width: 34%; background: var(--stripe-blue); }
  .stripe span:nth-child(3) { width: 33%; background: var(--stripe-teal); }
  .stripe-top { top: 0; }
  .stripe-bottom { top: 683px; }

  .hero {
    position: absolute; left: 0; top: 9px; width: 100%; height: 674px;
    background: linear-gradient(180deg, var(--sky-top) 0%, #bcd8ec 12%, var(--sky-mid) 38%, var(--sky-low) 100%);
  }

  .frost { position: absolute; border-radius: 50%;
    background: radial-gradient(circle, var(--frost) 0%, rgba(225,243,255,0) 70%); }

  .script { font-family: "Great Vibes", cursive; color: var(--navy); position: absolute; line-height: 1; }
  .headline-celebrate { left: 160px; top: 32px; font-size: 54px; }
  .headline-our { left: 166px; top: 100px; font-size: 44px; }
  .headline-anniversary { left: 168px; top: 262px; font-size: 72px; }

  .year-numeral {
    position: absolute; left: 228px; top: 72px;
    font-family: "PT Sans", sans-serif; font-weight: 700;
    font-size: 218px; line-height: 1; color: var(--navy);
  }
  .year-suffix {
    position: absolute; left: 289px; top: 242px;
    background: var(--navy); color: var(--white);
    font-weight: 700; font-size: 14px; line-height: 18px; padding: 0 5px;
  }

  .tagline { position: absolute; left: 120px; top: 320px; font-size: 21px; font-weight: 700; color: var(--cream); }
  .dates { position: absolute; left: 172px; top: 346px; font-size: 25px; font-weight: 700; color: var(--navy); }

  .promo-text {
    position: absolute; left: 137px; width: 310px;
    font-size: 10.6px; line-height: 14px; color: var(--navy);
  }
  .promo-text .mark { font-family: Georgia, serif; font-weight: 700; font-size: 30px; line-height: 0; vertical-align: -9px; }
  .promo-one { top: 412px; }
  .promo-two { top: 545px; left: 141px; }

  .footer-band { position: absolute; left: 0; top: 692px; width: 100%; height: 124px; }

  .brand-square { position: absolute; left: 137px; top: 712px; width: 34px; height: 34px; background: var(--band-blue); }
  .brand-name {
    position: absolute; left: 83px; top: 758px; width: 150px; text-align: center;
    font-family: "Cinzel", serif; font-weight: 600; color: var(--navy);
    font-size: 16px; line-height: 18px;
  }
  .brand-name small { display: block; font-size: 11px; letter-spacing: 3px; }

  .address {
    position: absolute; left: 252px; top: 722px; width: 310px;
    font-family: "Noto Serif TC", serif; color: var(--ink-dark); text-align: right;
  }
  .address-en { font-size: 9.5px; line-height: 14px; }
  .address-zh { font-size: 12px; line-height: 18px; }

  .website {
    position: absolute; left: 275px; top: 780px; width: 270px; text-align: center;
    font-family: "Cinzel", serif; color: var(--white); font-size: 14px; letter-spacing: 3px;
  }
</style>
</head>
<body>
  <main class="flyer">
    <div class="stripe stripe-top"><span></span><span></span><span></span></div>

    <section class="hero">
      <div class="frost" role="img" aria-label="Silver star ornament" style="left:-20px;top:-10px;width:170px;height:170px"></div>
      <div class="frost" role="img" aria-label="Light blue snowflake ornament" style="left:370px;top:-15px;width:180px;height:120px"></div>
      <div class="frost" role="img" aria-label="Silver star ornament" style="left:460px;top:140px;width:130px;height:170px"></div>
      <div class="frost" role="img" aria-label="Light blue snowflake ornament" style="left:0;top:250px;width:140px;height:140px"></div>
      <div class="frost" role="img" aria-label="Light blue snowflake ornament" style="left:480px;top:395px;width:110px;height:130px"></div>
      <div class="frost" role="img" aria-label="Silver star ornament" style="left:-20px;top:395px;width:120px;height:130px"></div>
      <div class="frost" role="img" aria-label="Silver star ornament" style="left:490px;top:590px;width:100px;height:110px"></div>

      <div class="script headline-celebrate">Let's celebrate</div>
      <div class="script headline-our">our</div>
      <div class="year-numeral">2</div>
      <div class="year-suffix">nd Year</div>
      <div class="script headline-anniversary">anniversury</div>

      <p class="tagline">Come and Spend a day with us</p>
      <p class="dates">Now until 31st Dec 2024</p>
    </section>

    <p class="promo-text promo-one"><span class="mark">&ldquo;</span> Lorem ipsum dolor sit amet, consectetur adipiscing elit. Curabitur feugiat quis quam eget sodales. Cras iaculis posuere arcu quis venenatis. Maecenas tellus urna, pretium ac lacus sed, auctor fermentum est. Sed non dui velit. Integer quis blandit orci. Curabitur ornare risus tellus, vitae vestibulum leo imperdiet sit amet. Aenean tempor.<span class="mark">&rdquo;</span></p>

    <p class="promo-text promo-two"><span class="mark">&ldquo;</span> Lorem ipsum dolor sit amet, consectetur adipiscing elit. Curabitur feugiat quis quam eget sodales. Cras iaculis posuere arcu quis venenatis. Maecenas tellus urna, pretium ac lacus sed, auctor fermentum est. Sed non dui velit. Integer quis blandit orci. Curabitur ornare risus tellus, vitae vestibulum leo imperdiet sit amet. Aenean tempor.<span class="mark">&rdquo;</span></p>

    <div class="stripe stripe-bottom"><span></span><span></span><span></span></div>

    <svg class="footer-band" viewBox="0 0 577 124" width="577" height="124" aria-hidden="true">
      <rect x="0" y="0" width="577" height="124" fill="#ffffff"/>
      <polygon points="0,73 577,73 577,124 0,124" fill="#1c7cc6"/>
      <polygon points="75,73 245,73 215,124 40,124" fill="#ffffff"/>
    </svg>

    <div class="brand-square"></div>
    <div class="brand-name">COPPERLEAF<small>DENTAL</small></div>

    <div class="address">
      <p class="address-en">Unit 12, Harbourview Plaza, 88 Lantern Road, Kowloon</p>
      <p class="address-zh">九龍燈籠道88號海景廣場12室</p>
    </div>

    <p class="website">www.copperleaf.com.hk</p>
  </main>
</body>
</html>
```